Morvale Cosmetic Clinic Design

Hi there,

I offer a new set of packages in my cosmetic clinic. It is a down to earth clinic that provides natural results. My clinic has got a natural look.
My website is www.morvale.co.nz
I need one A4 flat leaflet for every package and the special. The leaflets can look of similar design.
Preferred colors are blue/white/silver and green.

```html
<!DOCTYPE html>
<html lang="en">
<head>
<meta charset="utf-8">
<title>Morvale Cosmetic Clinic – Male Pattern Baldness Packages</title>
<link rel="stylesheet" href="https://fonts.googleapis.com/css2?family=Lato:wght@300;400;700&family=Tinos:wght@400&family=Open+Sans:wght@700&display=swap">
<style>
:root{
  --blue:#1a9fd8;
  --blue-deep:#1283c2;
  --blue-soft:#bfe4f7;
  --card:#9fd6f1;
  --ink:#4a4f55;
  --silver:#a9adb2;
  --white:#ffffff;
}
*{margin:0;padding:0;box-sizing:border-box}
html,body{width:862px;height:1200px;overflow:hidden;background:var(--white)}
.leaflet{position:relative;width:862px;height:1200px;overflow:hidden;font-family:"Lato",Arial,sans-serif;color:var(--ink)}
.trim{position:absolute;background:#999}
.trim.h{height:1px;width:14px}
.trim.v{width:1px;height:14px}
.backdrop{position:absolute;left:24px;top:24px;width:814px;height:1152px}
.title{position:absolute;left:79px;top:602px;font-weight:300;color:var(--blue);font-size:31px;line-height:38px;letter-spacing:.3px}
.subtitle{position:absolute;left:79px;top:678px;font-weight:400;font-size:25px;color:var(--ink)}
.rule{position:absolute;left:79px;top:720px;width:172px;height:1px;background:var(--blue)}
.intro{position:absolute;left:79px;top:738px;width:460px;font-size:15.5px;line-height:21px;color:var(--ink)}
.intro p+p{margin-top:21px}
.brand{position:absolute;left:56px;top:1012px;display:flex;align-items:center;gap:12px}
.brand-dot{width:48px;height:48px;border-radius:50%;background:var(--blue-soft)}
.brand-name{font-family:"Lato",Arial,sans-serif;font-weight:300;font-size:21px;letter-spacing:1.5px;color:var(--silver);line-height:1}
.contact{position:absolute;left:79px;top:1074px;color:var(--ink)}
.web{font-size:21px;font-weight:400;letter-spacing:.3px}
.lines{margin-top:6px;font-size:12px;display:flex;gap:12px;align-items:center}
.lines span{display:inline-flex;align-items:center;gap:4px}
.lines svg{width:13px;height:13px}
.address{font-size:12px;margin-top:4px}
.pack{position:absolute;left:571px;width:257px;background:var(--card);border:3px solid var(--white);border-radius:6px;box-shadow:0 2px 5px rgba(0,0,0,.25);text-align:center;color:#2c4a5c;font-family:"Open Sans",Arial,sans-serif;font-weight:700;font-size:7.4px;line-height:9.5px;text-transform:uppercase;padding:0 10px 7px}
.pack-tab{margin:5px -18px 7px;background:var(--blue);color:var(--white);font-family:"Tinos",serif;font-weight:400;font-size:16px;line-height:27px;border-radius:3px;box-shadow:0 2px 3px rgba(0,0,0,.25);text-transform:uppercase}
.save{font-family:"Tinos",serif;font-weight:400;font-size:25px;line-height:29px;color:var(--blue-deep);margin:1px 0 3px}
.gap{margin-top:7px}
</style>
</head>
<body>
<div class="leaflet">
  <i class="trim h" style="left:0;top:24px"></i><i class="trim h" style="right:0;top:24px"></i>
  <i class="trim h" style="left:0;bottom:24px"></i><i class="trim h" style="right:0;bottom:24px"></i>
  <i class="trim v" style="left:24px;top:0"></i><i class="trim v" style="right:24px;top:0"></i>
  <i class="trim v" style="left:24px;bottom:0"></i><i class="trim v" style="right:24px;bottom:0"></i>

  <svg class="backdrop" viewBox="0 0 814 1152" width="814" height="1152">
    <defs>
      <radialGradient id="bokeh" cx="60%" cy="60%" r="70%">
        <stop offset="0" stop-color="#ffffff"/>
        <stop offset=".6" stop-color="#d7eefa"/>
        <stop offset="1" stop-color="#b6def4"/>
      </radialGradient>
      <linearGradient id="photoTone" x1="0" y1="0" x2="1" y2="1">
        <stop offset="0" stop-color="#f3f3f2"/>
        <stop offset=".45" stop-color="#c9a48c"/>
        <stop offset=".75" stop-color="#5b5a52"/>
        <stop offset="1" stop-color="#e9eaea"/>
      </linearGradient>
      <linearGradient id="whiteFade" x1="0" y1="0" x2="1" y2="0">
        <stop offset="0" stop-color="#ffffff" stop-opacity=".95"/>
        <stop offset=".8" stop-color="#ffffff" stop-opacity=".8"/>
        <stop offset="1" stop-color="#ffffff" stop-opacity=".4"/>
      </linearGradient>
    </defs>
    <rect width="814" height="1152" fill="url(#bokeh)"/>
    <g role="img" aria-label="Photograph of a smiling bearded man with tied-back hair, on a pale background with faint leaf shapes">
      <path d="M0 0H814V230C640 290 420 330 200 420C120 455 50 500 0 540Z" fill="url(#photoTone)"/>
    </g>
    <path d="M0 540C60 490 140 450 220 420C430 340 650 300 814 200V262C640 330 430 360 250 420C150 455 70 500 0 560Z" fill="#cfeaf8"/>
    <path d="M0 560C70 505 160 460 260 425C440 370 640 330 814 262" fill="none" stroke="#9fd2ee" stroke-width="3"/>
    <path d="M0 575C250 520 520 560 540 720C555 850 525 1000 480 1152H0Z" fill="url(#whiteFade)"/>
    <path d="M0 1120C180 1112 360 1124 470 1152" fill="none" stroke="#7fc6ec" stroke-width="2.5"/>
    <circle cx="160" cy="480" r="90" fill="#ffffff"/>
    <circle cx="160" cy="480" r="90" fill="none" stroke="#b4b8bc" stroke-width="5"/>
    <circle cx="160" cy="480" r="57" fill="var(--blue-soft)"/>
  </svg>

  <h1 class="title">MALE<br>PATTERN BALDNESS</h1>
  <h2 class="subtitle">Packages</h2>
  <div class="rule"></div>
  <div class="intro">
    <p>We are pleased to offer the following packages for the treatment of male pattern baldness.<br>Please bear in mind that combination treatments have got a higher chance of success.</p>
    <p>We offer monthly or weekly payment options. Please talk to us for more information.</p>
  </div>

  <div class="brand">
    <span class="brand-dot"></span>
    <span class="brand-name">MORVALE COSMETIC CLINIC</span>
  </div>

  <div class="contact">
    <div class="web">www.morvale.co.nz</div>
    <div class="lines">
      <span><svg viewBox="0 0 16 16"><circle cx="8" cy="8" r="8" fill="#1a9fd8"/><path d="M5 4l2 2-1 1c.5 1.2 1.8 2.5 3 3l1-1 2 2-1.5 1.5C7 12 4 9 3.5 5.5Z" fill="#fff"/></svg>0800 555 014</span>
      <span><svg viewBox="0 0 16 16"><circle cx="8" cy="8" r="8" fill="#1a9fd8"/><rect x="4" y="5" width="8" height="6" fill="#fff"/><path d="M4 5l4 3.5L12 5" fill="none" stroke="#1a9fd8" stroke-width="1"/></svg>hello@morvale.co.nz</span>
    </div>
    <div class="address">4/12 Harbour Lane Riverside Christchurch 8011</div>
  </div>

  <section class="pack" style="top:426px">
    <div class="pack-tab">Starter Pack</div>
    <div>All Regrova hair care products</div>
    <div>Regrova Light Cap &nbsp;$1135</div>
    <div class="save">SAVE 10%</div>
  </section>

  <section class="pack" style="top:555px">
    <div class="pack-tab">Basic Pack</div>
    <div>All Regrova hair care products</div>
    <div>Regrova Light Cap</div>
    <div class="save">SAVE 15%</div>
    <div>4 appointments with our aesthetic doctor</div>
    <div>Repeat prescriptions &amp; treatment overview $1975</div>
    <div class="gap">Maintenance $ 760 per year</div>
    <div>Get all products 15% off</div>
  </section>

  <section class="pack" style="top:728px">
    <div class="pack-tab">Advanced Pack</div>
    <div>All Regrova hair care products</div>
    <div>Regrova Light Cap</div>
    <div class="save">SAVE 20%</div>
    <div>4 appointments with our aesthetic doctor</div>
    <div>Repeat prescriptions and treatment overview</div>
    <div class="gap">4 plasma treatments with microneedling</div>
    <div>to further boost hair growth $2068</div>
    <div class="gap">Get all products 15% off</div>
    <div>Get 20% off all further plasma treatments</div>
    <div>and doctor's appointments</div>
  </section>

  <section class="pack" style="top:940px">
    <div class="pack-tab">Super Advanced Pack</div>
    <div>All Regrova hair care products</div>
    <div>Regrova Light Cap</div>
    <div class="save">SAVE 25%</div>
    <div>4 appointments with our aesthetic doctor</div>
    <div>Repeat prescriptions and treatment overview</div>
    <div class="gap">8 plasma treatments with microneedling</div>
    <div>to further boost hair growth $3776</div>
    <div class="gap">Get all products 15% off</div>
    <div>Get 20% off all further plasma treatments</div>
    <div>and doctor's appointments</div>
  </section>
</div>
</body>
</html>
```